VORETH FLYER 2019

Hi, We need an A4 flyer design for our cleaning company, focusing on dry carpet cleaning I attached our catalogue to give some idea. In addition, our websites can provide more information. Our Services:-General Cleaning Carry out heavy cleansing tasks and special projects. Clean, stock and supply designated facility areas (dusting, sweeping, vacuuming, mopping, cleaning ceiling vents, restroom cleaning etc).Using electrically powered scrubbing and polishing machines to burnish, scrub, polish and spray clean floors. Window Cleaning Regular, Reliable Window Cleaning. Hard To Reach Windows. Single 7 Multi-Storey. Frames and Glass Cleaned. Floor Cleaning Marble Cleaning & Polishing. Tile & Grout Cleaning. Hardwood Floors Services. Vinyl Floors. The BRIM Dry Extraction Carpet Cleaning System uses environmentally preferred, Clear Mark Certified cleaning products that deep cleans your carpets and textured hard floors quickly and easily.

Target Market(s)

Residential and Commercial.
Offices, Hospitals, Restaurants, Etc.

Industry/Entity Type

Cleaning Service

Font styles to use
Serif
Sans Serif

Colors
33a6d7
0592cd
85cae6
85acd3
3277b5
296eb1

Requirements
Must have
• CREATIVE AND MINIMAL
Nice to have
• Engaging Pics and Texts

```html
<!DOCTYPE html>
<html lang="en">
<head>
<meta charset="utf-8">
<title>Voreth Cleaning &amp; Maintenance Flyer</title>
<link rel="stylesheet" href="https://fonts.googleapis.com/css2?family=Montserrat:wght@600;700;800&family=Roboto+Condensed:wght@400;700&display=swap">
<style>
  :root {
    --navy: #25236e;
    --blue: #296eb1;
    --blue-bright: #3277b5;
    --sky: #85cae6;
    --sky-deep: #33a6d7;
    --slate: #58585a;
    --ink: #555558;
    --band: #dcdcdf;
    --stage: #ececef;
    --white: #ffffff;
  }
  html, body {
    margin: 0;
    padding: 0;
    width: 837px;
    height: 1200px;
    overflow: hidden;
    background: var(--stage);
  }
  .flyer {
    position: absolute;
    left: 0;
    top: 8px;
    width: 837px;
    height: 1183px;
    display: block;
  }
  .brand-name { font-family: 'Roboto Condensed', sans-serif; font-weight: 700; font-size: 66px; fill: var(--navy); }
  .tab-title { font-family: 'Roboto Condensed', sans-serif; font-weight: 700; fill: var(--white); }
  .floor-item { font-family: 'Roboto Condensed', sans-serif; font-size: 28px; fill: var(--white); }
  .task-label { font-family: 'Roboto Condensed', sans-serif; font-size: 30px; fill: var(--ink); }
  .service-item { font-family: 'Roboto Condensed', sans-serif; font-size: 28px; fill: var(--ink); }
  .headline { font-family: 'Roboto Condensed', sans-serif; font-weight: 700; font-size: 60px; fill: var(--white); }
  .headline-accent { font-family: 'Montserrat', sans-serif; font-weight: 800; font-size: 94px; fill: var(--sky); }
  .call-label { font-family: 'Montserrat', sans-serif; font-weight: 700; font-size: 30px; fill: var(--white); }
  .call-number { font-family: 'Roboto Condensed', sans-serif; font-size: 84px; fill: var(--white); }
  .contact-item { font-family: 'Montserrat', sans-serif; font-weight: 600; font-size: 19px; fill: var(--white); }
  .web-address { font-family: 'Montserrat', sans-serif; font-weight: 700; font-size: 40px; fill: var(--white); }
  .photo-kitchen { fill: url(#kitchenTone); }
  .photo-lounge { fill: url(#loungeTone); }
  .photo-parlour { fill: url(#parlourTone); }
</style>
</head>
<body>
<svg class="flyer" viewBox="0 0 1460 2064" xmlns="http://www.w3.org/2000/svg">
  <defs>
    <linearGradient id="kitchenTone" x1="0" y1="0" x2="0" y2="1">
      <stop offset="0" stop-color="#e9e9ee"/>
      <stop offset="0.55" stop-color="#f4f2ef"/>
      <stop offset="1" stop-color="#8e8278"/>
    </linearGradient>
    <linearGradient id="loungeTone" x1="0" y1="0" x2="0" y2="1">
      <stop offset="0" stop-color="#d9d9db"/>
      <stop offset="0.45" stop-color="#4a4a4d"/>
      <stop offset="1" stop-color="#1f1f21"/>
    </linearGradient>
    <linearGradient id="parlourTone" x1="0" y1="0" x2="1" y2="1">
      <stop offset="0" stop-color="#e6e4e2"/>
      <stop offset="0.4" stop-color="#5c5a5c"/>
      <stop offset="0.8" stop-color="#6e7a86"/>
      <stop offset="1" stop-color="#4f5e6c"/>
    </linearGradient>
    <linearGradient id="paperTone" x1="0" y1="0" x2="1" y2="0">
      <stop offset="0" stop-color="#f1f1f4"/>
      <stop offset="1" stop-color="#ffffff"/>
    </linearGradient>
  </defs>

  <rect class="page" x="0" y="0" width="1460" height="2064" fill="url(#paperTone)"/>

  <g class="header-frame">
    <polygon points="0,0 325,0 0,330" fill="var(--blue)"/>
    <polygon points="1115,0 1460,0 1460,349" fill="var(--slate)"/>
    <polygon points="0,679 0,944 275,944" fill="var(--slate)"/>
    <polygon points="1460,669 1460,944 1185,944" fill="var(--blue)"/>
  </g>

  <g class="header-photos">
    <polygon class="photo-kitchen" role="img" aria-label="Photo of a bright white kitchen with island and bar stools"
      points="0,340 283,68 718,494 278,934 0,669"/>
    <polygon class="photo-lounge" role="img" aria-label="Photo of a modern lounge with wall-mounted TV and sofas"
      points="306,0 1106,0 731,478"/>
    <polygon class="photo-parlour" role="img" aria-label="Photo of an elegant living room with sofa, mirror and tufted ottomans"
      points="1172,69 1460,359 1460,659 1185,934 742,494"/>
  </g>

  <g class="brand" text-anchor="middle">
    <text class="brand-name" x="730" y="880">VORETH CLEANING</text>
    <text class="brand-name" x="730" y="956">&amp; MAINTENANCE</text>
  </g>

  <polygon class="floor-panel" points="0,961 280,961 1145,1889 0,1889" fill="var(--navy)"/>
  <polygon class="floor-tab" points="0,1069 390,1069 325,1134 0,1134" fill="var(--sky)"/>
  <text class="tab-title" x="47" y="1119" font-size="40">FLOOR SERVICES</text>

  <g class="floor-list">
    <g fill="var(--sky-deep)">
      <circle cx="53" cy="1170" r="6"/>
      <circle cx="53" cy="1219" r="6"/>
      <circle cx="53" cy="1268" r="6"/>
      <circle cx="53" cy="1317" r="6"/>
      <circle cx="53" cy="1367" r="6"/>
      <circle cx="53" cy="1450" r="6"/>
      <circle cx="53" cy="1532" r="6"/>
    </g>
    <text class="floor-item" x="75" y="1179">Tile &amp; Grout Cleaning.</text>
    <text class="floor-item" x="75" y="1228">Hardwood Floors Services.</text>
    <text class="floor-item" x="75" y="1277">Vinyl Floors.</text>
    <text class="floor-item" x="75" y="1326">Floor Cleaning Marble Cleaning &amp; Polishing.</text>
    <text class="floor-item" x="75" y="1376">Using electrically powered scrubbing &amp; polishing</text>
    <text class="floor-item" x="75" y="1408">machines to burnish, scrub, polish &amp; spray clean floors.</text>
    <text class="floor-item" x="75" y="1459">The BRIM Dry Extraction Carpet Cleaning System uses</text>
    <text class="floor-item" x="75" y="1491">environmentally preferred.</text>
    <text class="floor-item" x="75" y="1541">Clear Mark Certified cleaning products that deep cleans your</text>
    <text class="floor-item" x="75" y="1573">carpets &amp; textured hard floors quickly &amp; easily.</text>
  </g>

  <g class="headline-block">
    <text class="headline" x="62" y="1679">GENERAL CLEANING CARRY OUT</text>
    <text class="headline" x="62" y="1746">HEAVY CLEANSING TASKS AND</text>
    <text class="headline-accent" x="62" y="1838" textLength="900" lengthAdjust="spacingAndGlyphs">SPECIAL PROJECTS</text>
  </g>

  <polygon class="task-tab" points="500,1082 1412,1082 1412,1137 555,1137" fill="var(--slate)"/>
  <text class="tab-title" x="1393" y="1121" font-size="40" text-anchor="end">STOCK AND SUPPLY DESIGNATED FACILITY AREAS</text>

  <g class="task-icons" fill="var(--navy)" stroke="var(--blue-bright)" stroke-width="3">
    <circle cx="660" cy="1202" r="37"/>
    <circle cx="893" cy="1202" r="37"/>
    <circle cx="1127" cy="1202" r="37"/>
    <circle cx="1359" cy="1202" r="37"/>
    <circle cx="903" cy="1364" r="37"/>
    <circle cx="1254" cy="1364" r="37"/>
  </g>
  <g class="task-glyphs" fill="none" stroke="var(--white)" stroke-width="4" stroke-linecap="round" stroke-linejoin="round">
    <path d="M648 1222 L668 1186 M662 1190 l14 -6 M660 1198 l14 -4 M657 1206 l13 -2"/>
    <path d="M900 1182 L888 1212 M878 1212 h24 l4 10 h-32 z"/>
    <path d="M1112 1218 h22 a8 8 0 0 0 0 -16 h-14 M1120 1202 L1138 1184 v-4"/>
    <path d="M1347 1200 h24 l-4 22 h-16 z M1362 1200 L1370 1180"/>
    <path d="M903 1344 c-10 14 -14 20 -14 27 a14 14 0 0 0 28 0 c0 -7 -4 -13 -14 -27 z"/>
    <path d="M1238 1346 h32 v36 h-32 z M1244 1356 h20 M1244 1364 h20 M1244 1372 h20"/>
  </g>
  <g class="task-labels" text-anchor="middle">
    <text class="task-label" x="660" y="1274">Dusting</text>
    <text class="task-label" x="893" y="1274">Sweeping</text>
    <text class="task-label" x="1127" y="1274">Vacuuming</text>
    <text class="task-label" x="1359" y="1274">Mopping</text>
    <text class="task-label" x="903" y="1437">Restroom Cleaning</text>
    <text class="task-label" x="1254" y="1437">Cleaning Ceiling Vents</text>
  </g>

  <rect class="services-rule" x="785" y="1496" width="290" height="10" fill="var(--slate)"/>
  <polygon class="services-tab" points="1065,1496 1412,1496 1412,1561 1130,1561" fill="var(--slate)"/>
  <text class="tab-title" x="1393" y="1545" font-size="44" text-anchor="end">OUR SERVICES</text>

  <g class="services-list">
    <g fill="var(--sky-deep)">
      <circle cx="1107" cy="1600" r="6"/>
      <circle cx="1107" cy="1650" r="6"/>
      <circle cx="1107" cy="1700" r="6"/>
      <circle cx="1107" cy="1750" r="6"/>
      <circle cx="1107" cy="1800" r="6"/>
    </g>
    <text class="service-item" x="1125" y="1609">Window Cleaning Regular.</text>
    <text class="service-item" x="1125" y="1659">Reliable Window Cleaning.</text>
    <text class="service-item" x="1125" y="1709">Hard To Reach Windows.</text>
    <text class="service-item" x="1125" y="1759">Frames &amp; Glass Cleaned.</text>
    <text class="service-item" x="1125" y="1809">Single 7 Multi-Storey.</text>
  </g>

  <g class="footer">
    <rect x="65" y="1902" width="1395" height="57" fill="var(--band)"/>
    <polygon points="875,1979 1460,1979 1460,2064 960,2064" fill="var(--slate)"/>
    <polygon points="0,1854 90,1939 845,1939 960,2064 0,2064" fill="var(--blue)"/>

    <text class="call-label" x="47" y="1994">CALL US</text>
    <text class="call-label" x="47" y="2029">TODAY</text>
    <text class="call-number" x="183" y="2031" textLength="377" lengthAdjust="spacingAndGlyphs">123-456-789</text>
    <line x1="595" y1="1954" x2="595" y2="2049" stroke="var(--white)" stroke-width="2"/>

    <g class="contact-icons" fill="var(--white)">
      <circle cx="641" cy="1972" r="8"/>
      <circle cx="641" cy="2001" r="8"/>
      <circle cx="641" cy="2030" r="8"/>
    </g>
    <g fill="var(--blue)">
      <circle cx="641" cy="1970" r="3"/>
      <rect x="638" y="1996" width="6" height="10" rx="1.5"/>
      <rect x="636" y="2027" width="10" height="6"/>
    </g>
    <text class="contact-item" x="662" y="1979">Address Goes Here</text>
    <text class="contact-item" x="662" y="2008">Phone no Goes Here</text>
    <text class="contact-item" x="662" y="2037">Mail Goes Here</text>

    <g class="globe" fill="none" stroke="var(--white)" stroke-width="3">
      <circle cx="982" cy="2022" r="20"/>
      <ellipse cx="982" cy="2022" rx="9" ry="20"/>
      <line x1="962" y1="2022" x2="1002" y2="2022"/>
      <line x1="966" y1="2011" x2="998" y2="2011"/>
      <line x1="966" y1="2033" x2="998" y2="2033"/>
    </g>
    <text class="web-address" x="1020" y="2039" textLength="390" lengthAdjust="spacingAndGlyphs">www.vorethclean.com</text>
  </g>
</svg>
</body>
</html>
```